Sparrow Haulage needs a business card design.

Design a double-sided business card for new freight business. On the front, would like to see our logo along with the following info:

Martin Obuya
CEO/FOUNDER
555-206-7142
martinobuya@sparrow-haulage.example

On the reverse side, we would like to use the graphic image of our logo only without the Sparrow Haulage name.

```html
<!DOCTYPE html>
<html lang="en">
<head>
<meta charset="utf-8">
<title>Sparrow Haulage – Business Card</title>
<link href="https://fonts.googleapis.com/css2?family=Arimo:wght@400;700&display=swap" rel="stylesheet">
<style>
  :root {
    --navy: #03045e;
    --red: #b40000;
    --white: #ffffff;
    --ink: #1c1c1c;
    --stage: #2b2b2b;
  }
  html, body {
    margin: 0;
    padding: 0;
    width: 1200px;
    height: 1040px;
    overflow: hidden;
    background: var(--stage);
    font-family: "Arimo", Arial, sans-serif;
  }
  .stage {
    position: relative;
    width: 1200px;
    height: 1040px;
  }
  .card {
    position: absolute;
    left: 250px;
    width: 700px;
    height: 400px;
    box-sizing: border-box;
    box-shadow: 0 10px 30px rgba(0,0,0,0.5);
  }
  .card-back {
    top: 90px;
    background: var(--navy);
    border-radius: 70px 0 70px 0;
    display: flex;
    align-items: center;
    justify-content: center;
  }
  .logo-symbol {
    width: 150px;
    height: 150px;
    border-radius: 50%;
    background: var(--white);
  }
  .card-front {
    top: 550px;
    background: var(--white);
    border-radius: 0 70px 0 70px;
    padding: 56px 0 0 130px;
  }
  .brand-front {
    display: flex;
    align-items: center;
    gap: 18px;
    color: var(--navy);
    font-weight: 700;
    font-size: 40px;
    letter-spacing: 9px;
    line-height: 1;
    text-transform: uppercase;
  }
  .brand-front .brand-dot {
    width: 60px;
    height: 60px;
    border-radius: 50%;
    background: var(--navy);
    flex: none;
  }
  .person {
    margin-top: 40px;
    padding-left: 70px;
  }
  .person-name {
    margin: 0;
    font-weight: 700;
    font-size: 32px;
    letter-spacing: 0.5px;
    line-height: 1.1;
    text-transform: uppercase;
  }
  .person-name .first { color: var(--navy); }
  .person-name .last { color: var(--red); }
  .person-role {
    margin: 2px 0 0;
    font-size: 24px;
    color: var(--ink);
    letter-spacing: 0.5px;
  }
  .contacts {
    list-style: none;
    margin: 22px 0 0;
    padding: 0 0 0 50px;
    font-size: 22px;
    color: var(--ink);
  }
  .contacts li {
    display: flex;
    align-items: center;
    gap: 12px;
    line-height: 32px;
  }
  .contacts svg {
    width: 20px;
    height: 20px;
    flex: none;
  }
  .web-a { color: var(--navy); }
  .web-b { color: var(--red); }
</style>
</head>
<body>
<main class="stage">

  <section class="card card-back" aria-label="Business card reverse">
    <div class="logo-symbol" role="img" aria-label="Sparrow Haulage logo symbol"></div>
  </section>

  <section class="card card-front" aria-label="Business card front">
    <div class="brand-front">
      <span class="brand-dot"></span>
      <span>Sparrow Haulage</span>
    </div>

    <div class="person">
      <h1 class="person-name"><span class="first">Martin</span> <span class="last">Obuya</span></h1>
      <p class="person-role">CEO/FOUNDER</p>
    </div>

    <ul class="contacts">
      <li>
        <svg viewBox="0 0 24 24" aria-hidden="true"><path fill="#b40000" d="M6.6 10.8a15.1 15.1 0 0 0 6.6 6.6l2.2-2.2c.3-.3.7-.4 1-.2 1.1.4 2.3.6 3.6.6.6 0 1 .4 1 1V20c0 .6-.4 1-1 1A17 17 0 0 1 3 4c0-.6.4-1 1-1h3.5c.6 0 1 .4 1 1 0 1.3.2 2.5.6 3.6.1.3 0 .7-.2 1z"/></svg>
        <span>555-206-7142</span>
      </li>
      <li>
        <svg viewBox="0 0 24 24" aria-hidden="true"><rect x="2" y="5" width="20" height="14" fill="#b40000"/><path d="M2 5l10 8 10-8" fill="none" stroke="#fff" stroke-width="1.6"/></svg>
        <span>martinobuya@sparrow-haulage.example</span>
      </li>
      <li>
        <svg viewBox="0 0 24 24" aria-hidden="true"><g fill="none" stroke="#b40000" stroke-width="2"><circle cx="12" cy="12" r="9"/><ellipse cx="12" cy="12" rx="4" ry="9"/><path d="M3 12h18M5 7h14M5 17h14"/></g></svg>
        <span>www.<span class="web-a">sparrow</span>-<span class="web-b">haulage</span>.example</span>
      </li>
    </ul>
  </section>

</main>
</body>
</html>
```